New Business Card Design Project LORVANTI-Italy

we are LORVANTI-Italy
our company in the market for 3 years we are luxury cosmetic company and its about time for a facelift :)
i will like to have elegant luxurious and unique business card
that will give the person that get it a unique, luxurious and elegant impression
I'm VERY OPEN FOR NEW IDEAS , even duo i add a few files of things that i see on line and i like them

i add my logo as well
my website is LORVANTI.COM
(if you would like to see the main style that we have)

Target Market(s)

adult that have money :)

Industry/Entity Type

Business

Contact Information for Business Card

Name - Dario Lorvanti
Position - CEO and CO Founder
address - 4817 E Halvern
telephone - 555-384-1926
email - dario@lorvanti.com
fax - 555-384-1926
website - LORVANTI.COM

Colors
000000
959595
fbee3e
ffffff

Requirements
Must have
• big logo in GOLD color
• elegant look
• impressive
Nice to have
• not must but maybe classy pattern background
• not must but maybe emblem
• maybe clear plastic business card
Should not have
• colors
• images

```html
<!DOCTYPE html>
<html lang="en">
<head>
<meta charset="utf-8">
<title>LORVANTI Italy – Business Card</title>
<link rel="stylesheet" href="https://fonts.googleapis.com/css2?family=Montserrat:wght@400;500;600&display=swap">
<style>
  :root {
    --backdrop: #141414;
    --card: #1e1e1e;
    --card-back: #1b1b1b;
    --gold: #d4a52a;
    --gold-soft: #3a3a3a;
    --ink: #ffffff;
    --muted: #959595;
  }
  * { margin: 0; padding: 0; box-sizing: border-box; }
  html, body {
    width: 1200px; height: 833px; overflow: hidden;
    background: var(--backdrop);
    font-family: "Montserrat", Arial, sans-serif;
  }
  .canvas { position: relative; width: 1200px; height: 833px; }
  .card {
    position: absolute; top: 268px;
    width: 520px; height: 297px;
    box-shadow: 0 18px 40px rgba(0,0,0,.55);
  }
  .card--back { left: 60px; background: var(--card-back); }
  .card--front { left: 620px; background: var(--card); }

  /* back: blind-pressed name mark */
  .back-mark {
    position: absolute; left: 50%; top: 50%; transform: translate(-50%, -50%);
    display: flex; flex-direction: column; align-items: center; gap: 12px;
  }
  .back-mark__circle {
    width: 96px; height: 96px; border-radius: 50%;
    border: 2px solid var(--gold-soft);
  }
  .back-mark__name {
    font-weight: 500; font-size: 18px; letter-spacing: 4px; color: var(--gold-soft);
  }

  /* front: brand lockup */
  .brand {
    position: absolute; left: 28px; top: 78px; width: 222px;
    display: flex; flex-direction: column; align-items: center;
  }
  .brand__circle {
    width: 76px; height: 76px; border-radius: 50%;
    border: 3px solid var(--gold);
    margin-bottom: 14px;
  }
  .brand__name {
    font-weight: 500; font-size: 30px; letter-spacing: 1px; color: var(--gold);
    line-height: 1;
  }
  .brand__place {
    margin-top: 10px;
    font-weight: 500; font-size: 12px; letter-spacing: 2px; color: var(--gold);
  }
  .divider {
    position: absolute; left: 268px; top: 70px;
    width: 1.5px; height: 158px; background: var(--gold);
  }

  /* front: contact details */
  .contact { position: absolute; left: 286px; top: 72px; color: var(--ink); }
  .contact__name { font-weight: 600; font-size: 19px; color: var(--gold); line-height: 1.1; }
  .contact__role { font-size: 12.5px; margin-top: 2px; }
  .contact__address { font-size: 12.5px; line-height: 1.4; margin-top: 12px; }
  .contact__list { list-style: none; margin-top: 10px; font-size: 12.5px; line-height: 1.4; }
  .contact__list li { display: flex; align-items: center; gap: 7px; }
  .contact__list svg { width: 11px; height: 11px; flex: none; }
</style>
</head>
<body>
<main class="canvas">
  <section class="card card--back" aria-label="Card back">
    <div class="back-mark">
      <div class="back-mark__circle"></div>
      <div class="back-mark__name">LORVANTI</div>
    </div>
  </section>

  <section class="card card--front" aria-label="Card front">
    <div class="brand">
      <div class="brand__circle"></div>
      <div class="brand__name">LORVANTI</div>
      <div class="brand__place">ITALY</div>
    </div>

    <div class="divider"></div>

    <div class="contact">
      <p class="contact__name">Dario Lorvanti</p>
      <p class="contact__role">Managing Partner</p>
      <p class="contact__address">Street Name Ave, Suite 100<br>State, Zip Code, Country</p>
      <ul class="contact__list">
        <li>
          <svg viewBox="0 0 12 12" aria-hidden="true"><path d="M2.5 1h2l1 3-1.3 1a7 7 0 0 0 2.8 2.8l1-1.3 3 1v2c0 .8-.7 1.5-1.5 1.5A9.5 9.5 0 0 1 1 2.5C1 1.7 1.7 1 2.5 1z" fill="#d4a52a"/></svg>
          012-345-6789
        </li>
        <li>
          <svg viewBox="0 0 12 12" aria-hidden="true"><rect x="3" y="0.8" width="6" height="10.4" rx="1" fill="none" stroke="#d4a52a" stroke-width="1.3"/><circle cx="6" cy="9.3" r=".7" fill="#d4a52a"/></svg>
          012-345-6780
        </li>
        <li>
          <svg viewBox="0 0 12 12" aria-hidden="true"><rect x=".8" y="2.5" width="10.4" height="7" fill="#d4a52a"/><path d="M.8 2.5 6 6.5l5.2-4" fill="none" stroke="#1e1e1e" stroke-width="1"/></svg>
          info@yourwebsite.com
        </li>
        <li>
          <svg viewBox="0 0 12 12" aria-hidden="true"><g fill="none" stroke="#d4a52a" stroke-width="1.1"><circle cx="6" cy="6" r="5"/><ellipse cx="6" cy="6" rx="2.2" ry="5"/><path d="M1 6h10M2 3.5h8M2 8.5h8"/></g></svg>
          yourwebsite.com
        </li>
      </ul>
    </div>
  </section>
</main>
</body>
</html>
```